Card design for orthopaedic surgeons working as The Brightwater Joint Centre

Business cards, letterhead

Colors

Designer to choose colors to be used in the design.

Requirements
Must have
• Late addition.
• Cards letterhead must have logos of
• Crestmoor Lindell College of Surgeons
• Varenwood Bone Health Association
Nice to have
• Back of card to have space for appointment time to be added by hand and some blank space for writing incidental other notes.

```html
<!DOCTYPE html>
<html lang="en">
<head>
<meta charset="utf-8">
<title>The Brightwater Joint Centre – Stationery</title>
<link rel="stylesheet" href="https://fonts.googleapis.com/css2?family=Montserrat:wght@300;400;500;600&family=Arimo:wght@400;700&display=swap">
<style>
  :root {
    --navy: #0c3049;
    --sky: #5aa0d4;
    --paper: #f5f5f5;
    --backdrop: #e3e3e3;
    --ink: #1b1b1b;
    --badge-gold: #c9a86a;
    --badge-grey: #b9b2a6;
  }
  * { box-sizing: border-box; margin: 0; padding: 0; }
  html, body { width: 1200px; height: 1200px; overflow: hidden; }
  body { background: var(--backdrop); position: relative; font-family: "Montserrat", sans-serif; }

  .sheet { position: absolute; background: var(--paper); overflow: hidden; }

  /* Letterhead */
  .letterhead { left: 98px; top: 124px; width: 678px; height: 957px; }
  .brand-name { position: absolute; font-family: "Montserrat", sans-serif; font-weight: 400; color: var(--navy); white-space: nowrap; letter-spacing: -0.2px; }
  .letterhead .brand-name { left: 47px; top: 70px; font-size: 21px; }
  .contact { position: absolute; text-align: right; color: var(--navy); font-weight: 300; }
  .letterhead .contact { right: 48px; top: 51px; font-size: 10px; line-height: 12.4px; }
  .contact .gap { height: 5px; }
  .contact svg { width: 8px; height: 8px; vertical-align: -1px; margin-left: 3px; }

  .letter { position: absolute; left: 47px; width: 583px; font-family: "Arimo", sans-serif; color: var(--ink); font-size: 9.8px; line-height: 13.7px; }
  .letter-date { top: 220px; }
  .letter-recipient { top: 247px; }
  .letter-salutation { top: 343px; font-weight: 700; }
  .letter-body { top: 384px; text-align: justify; }
  .letter-body p { margin-bottom: 13.5px; }
  .letter-closing { top: 685px; }
  .signature { position: absolute; left: 47px; top: 718px; width: 165px; height: 22px; background: linear-gradient(90deg, #d8d8d8, #ececec); border-radius: 3px; }
  .letter-signatory { top: 753px; }

  .badge { position: absolute; }
  .badge-college { left: 57px; top: 837px; width: 53px; height: 72px; border-radius: 26px 26px 8px 8px; background: linear-gradient(180deg, var(--badge-gold), #b3463b); }
  .badge-association { left: 145px; top: 843px; width: 50px; height: 62px; border-radius: 6px; background: linear-gradient(180deg, var(--badge-grey), #7f8fa6); }

  .wave { position: absolute; left: 0; bottom: 0; width: 100%; display: block; }
  .site { position: absolute; color: #fff; font-weight: 400; }
  .letterhead .site { left: 455px; bottom: 20px; font-size: 11px; letter-spacing: 0.2px; }

  /* Appointment card */
  .appointment-card { left: 824px; top: 280px; width: 291px; height: 177px; }
  .appointment-title { position: absolute; top: 22px; width: 100%; text-align: center; font-size: 10px; font-weight: 600; color: var(--navy); }
  .field { position: absolute; left: 21px; font-size: 7.5px; color: var(--navy); }
  .field-line { position: absolute; height: 0; border-top: 0.8px solid var(--sky); }
  .appointment-card .brand-name { left: 0; width: 100%; text-align: center; top: 148px; font-size: 9px; }

  /* Business card */
  .business-card { left: 824px; top: 506px; width: 291px; height: 177px; }
  .business-card .brand-name { left: 19px; top: 31px; font-size: 12.4px; }
  .holder-name { position: absolute; left: 19px; top: 76px; font-size: 10.5px; font-weight: 600; color: var(--sky); }
  .holder-title { position: absolute; left: 19px; top: 89px; font-size: 8px; color: var(--navy); }
  .business-card .contact { right: 17px; top: 100px; font-size: 7.6px; line-height: 9.5px; font-weight: 400; }
  .business-card .contact .gap { height: 4px; }
  .business-card .contact svg { width: 6px; height: 6px; }
  .business-card .badge-college { left: 20px; top: 115px; width: 28px; height: 37px; border-radius: 14px 14px 4px 4px; }
  .business-card .badge-association { left: 64px; top: 118px; width: 30px; height: 32px; border-radius: 4px; }
  .business-card .site { right: 18px; bottom: 7px; font-size: 7.5px; }
</style>
</head>
<body>

<section class="sheet letterhead" aria-label="Letterhead">
  <div class="brand-name">The Brightwater Joint Centre</div>
  <address class="contact" style="font-style:normal">
    <div>48 Harbour Lane</div>
    <div>Brightwater, 40217</div>
    <div class="gap"></div>
    <div>(555) 014-2641<svg viewBox="0 0 10 10"><path d="M2 0.8 L3.6 0.8 L4.3 3 L3.2 3.9 Q4.3 6 6.1 6.8 L7 5.7 L9.2 6.4 L9.2 8 Q9.2 9.2 8 9.2 Q0.8 8.6 0.8 2 Q0.8 0.8 2 0.8Z" fill="#5aa0d4"/></svg></div>
    <div>daniel@brightwaterjoint.com<svg viewBox="0 0 10 10"><rect x="0.6" y="2" width="8.8" height="6.2" fill="none" stroke="#5aa0d4" stroke-width="0.9"/><path d="M0.6 2 L5 5.6 L9.4 2" fill="none" stroke="#5aa0d4" stroke-width="0.9"/></svg></div>
  </address>

  <div class="letter letter-date">November 12, 2019</div>
  <div class="letter letter-recipient">Mr. Peter Lang<br>President<br>Ardent Holdings<br>111 Street Name, Suite#<br>City, State, 12345</div>
  <div class="letter letter-salutation">Dear Mr. Lang,</div>
  <div class="letter letter-body">
    <p>Lorem ipsum dolor sit amet, consectetur adipiscing elit. Integer diam quam, egestas eu ultrices eu, suscipit ac sapien. Phasellus eu dui nisi. Nam et euismod diam, nec lobortis tortor. Donec et diam nulla. Aenean varius tincidunt convallis. Aliquam a tortor at lacus dictum aliquet. Nunc laoreet metus sapien, in scelerisque augue consectetur in.</p>
    <p>Fusce nec justo laoreet, egestas justo sed, aliquet sem. Pellentesque pharetra massa non orci bibendum semper. Pellentesque cursus eu lectus a consectetur. Nunc volutpat suscipit posuere. Vestibulum facilisis vel quam malesuada mattis. Nulla in mattis tellus. Maecenas tristique mauris vitae pharetra tincidunt. In ut ornare risus. Integer molestie vestibulum nisi, semper dapibus mi condimentum eu.</p>
    <p>Nullam sagittis elit libero, id fringilla est tincidunt eget. Donec in ipsum ultricies, consectetur quam vel, facilisis elit. Phasellus tincidunt congue risus vel luctus. Suspendisse ut mollis neque. Donec ornare orci in turpis vestibulum, in ultrices metus scelerisque. Pellentesque mattis mattis nunc, nec tincidunt lacus egestas id. Fusce facilisis sagittis neque sit amet vulputate. Aliquam ut eros lobortis tortor facilisis vehicula. Sed sed luctus leo, at laoreet sapien. Donec placerat adipiscing ligula non euismod. In lobortis pretium nisl id luctus.</p>
    <p>Integer gravida tincidunt nibh, scelerisque tincidunt turpis. Suspendisse potenti. Nunc hendrerit euismod lectus id elementum. Fusce vitae gravida velit, quis eleifend lectus. In imperdiet mauris eu dui viverra sagittis. Donec tempor dui diam, condimentum gravida lacus pretium a. Nullam fringilla augue quis arcu placerat scelerisque. Aliquam nec tincidunt augue, sit amet posuere ipsum.</p>
  </div>
  <div class="letter letter-closing">Sincerely Yours,</div>
  <div class="signature" role="img" aria-label="Handwritten signature of Daniel Whitcombe"></div>
  <div class="letter letter-signatory">Daniel Whitcombe<br>Managing Director</div>

  <div class="badge badge-college" role="img" aria-label="Crestmoor Lindell College of Surgeons crest"></div>
  <div class="badge badge-association" role="img" aria-label="Varenwood Bone Health Association fellowship badge"></div>

  <svg class="wave" viewBox="0 0 678 72" preserveAspectRatio="none" height="72" aria-hidden="true">
    <path d="M0 6 C90 42 210 50 350 32 C480 14 610 8 678 32 L678 72 L0 72Z" fill="#5aa0d4"/>
    <path d="M0 36 C90 60 210 64 350 46 C480 30 610 24 678 34 L678 72 L0 72Z" fill="#ffffff"/>
    <path d="M0 39 C90 63 210 67 350 49 C480 33 610 27 678 37 L678 72 L0 72Z" fill="#0c3049"/>
  </svg>
  <div class="site">www.brightwaterjoint.com</div>
</section>

<section class="sheet appointment-card" aria-label="Appointment card">
  <div class="appointment-title">Next Appointment</div>
  <div class="field" style="top:65px">Name</div>
  <div class="field-line" style="left:48px; width:222px; top:74px"></div>
  <div class="field" style="top:91px">Date</div>
  <div class="field-line" style="left:48px; width:222px; top:100px"></div>
  <div class="field" style="left:180px; top:92px">Time</div>
  <div class="field" style="top:118px">Note</div>
  <div class="field-line" style="left:48px; width:222px; top:127px"></div>
  <div class="brand-name">The Brightwater Joint Centre</div>
</section>

<section class="sheet business-card" aria-label="Business card">
  <div class="brand-name">The Brightwater Joint Centre</div>
  <div class="holder-name">Daniel Whitcombe</div>
  <div class="holder-title">Managing Director</div>
  <address class="contact" style="font-style:normal">
    <div>48 Harbour Lane</div>
    <div>Brightwater, 40217</div>
    <div class="gap"></div>
    <div>(555) 014-2641<svg viewBox="0 0 10 10"><path d="M2 0.8 L3.6 0.8 L4.3 3 L3.2 3.9 Q4.3 6 6.1 6.8 L7 5.7 L9.2 6.4 L9.2 8 Q9.2 9.2 8 9.2 Q0.8 8.6 0.8 2 Q0.8 0.8 2 0.8Z" fill="#5aa0d4"/></svg></div>
    <div>daniel@brightwaterjoint.com<svg viewBox="0 0 10 10"><rect x="0.6" y="2" width="8.8" height="6.2" fill="none" stroke="#5aa0d4" stroke-width="0.9"/><path d="M0.6 2 L5 5.6 L9.4 2" fill="none" stroke="#5aa0d4" stroke-width="0.9"/></svg></div>
  </address>
  <div class="badge badge-college" role="img" aria-label="Crestmoor Lindell College of Surgeons crest"></div>
  <div class="badge badge-association" role="img" aria-label="Varenwood Bone Health Association fellowship badge"></div>
  <svg class="wave" viewBox="0 0 291 32" preserveAspectRatio="none" height="32" aria-hidden="true">
    <path d="M0 0 C40 18 100 20 160 12 C210 5 255 2 291 10 L291 32 L0 32Z" fill="#5aa0d4"/>
    <path d="M0 16 C40 28 100 28 160 20 C210 13 255 10 291 12 L291 32 L0 32Z" fill="#ffffff"/>
    <path d="M0 18 C40 30 100 30 160 22 C210 15 255 12 291 14 L291 32 L0 32Z" fill="#0c3049"/>
  </svg>
  <div class="site">www.brightwaterjoint.com</div>
</section>

</body>
</html>
```